Business Card for my New Brokerage

Looking to get a business card design for my new Real Estate Brokerage.
I want it with Picture, Phone Number, Email, Website, Office Address
Name and Designation. Please add logo too.

Target Market(s)

Real Estate Investors or Home Buyers

Industry/Entity Type

Real Estate

Contact Information for Business Card

Name, Email, Phone Number, website, email, office address

Colors
EB3D1F
EC4F4E
F09395
F8D3D4
FCEDEE

Requirements
Must have
• Minimalistic, Clean, Modern, Photo
Nice to have
• White and Red Colors

```html
<!DOCTYPE html>
<html lang="en">
<head>
<meta charset="utf-8">
<title>Ember Realty – Business Card</title>
<link rel="stylesheet" href="https://fonts.googleapis.com/css2?family=Montserrat:wght@400;500;600;800&display=swap">
<style>
  :root {
    --brand-red: #e00000;
    --gold: #c9a24a;
    --white: #ffffff;
    --ink: #1a1a1a;
    --backdrop: #2b2b2b;
    --suit-dark: #2a2a2a;
    --suit-mid: #4a4a4a;
  }
  * { box-sizing: border-box; margin: 0; padding: 0; }
  html, body { width: 1200px; height: 1015px; overflow: hidden; }
  body {
    background: var(--backdrop);
    font-family: "Montserrat", sans-serif;
    position: relative;
  }
  .card {
    position: absolute;
    left: 230px;
    width: 740px;
    height: 423px;
    overflow: hidden;
    box-shadow: 0 12px 30px rgba(0,0,0,.55);
  }
  .brand-name {
    font-weight: 800;
    letter-spacing: 1px;
    line-height: 1;
    white-space: nowrap;
  }
  /* Front */
  .card--front { top: 60px; background: var(--brand-red); }
  .card--front .brand-name {
    position: absolute;
    left: 80px;
    bottom: 90px;
    color: var(--white);
    font-size: 56px;
  }
  /* Back */
  .card--back { top: 533px; background: var(--brand-red); }
  .portrait {
    position: absolute;
    left: 60px; top: 70px;
    width: 330px; height: 353px;
    background: linear-gradient(180deg, var(--suit-mid) 0%, var(--suit-dark) 100%);
    border-radius: 120px 120px 0 0;
  }
  .info-panel {
    position: absolute;
    inset: 0;
    background: var(--white);
    clip-path: polygon(52% 0, 100% 0, 100% 100%, 68% 100%);
  }
  .divider {
    position: absolute;
    inset: 0;
    width: 100%; height: 100%;
  }
  .info {
    position: absolute;
    left: 440px;
    top: 44px;
    width: 290px;
    color: var(--ink);
  }
  .info .brand-name {
    color: var(--brand-red);
    font-size: 34px;
    margin-bottom: 44px;
  }
  .person__name {
    color: var(--brand-red);
    font-weight: 800;
    font-size: 24px;
    letter-spacing: .5px;
    margin-left: 60px;
    white-space: nowrap;
  }
  .person__title {
    font-size: 15px;
    font-weight: 500;
    margin: 2px 0 22px 60px;
  }
  .contact { list-style: none; margin-left: 60px; }
  .contact li {
    display: flex;
    align-items: center;
    gap: 8px;
    font-size: 14px;
    margin-bottom: 6px;
    white-space: nowrap;
  }
  .contact svg { width: 14px; height: 14px; fill: var(--brand-red); flex: none; }
  .contact .highlight { color: var(--brand-red); }
  .address {
    margin: 16px 0 0 82px;
    font-size: 14px;
    line-height: 1.35;
  }
</style>
</head>
<body>

<section class="card card--front" aria-label="Card front">
  <div class="brand-name">EMBER REALTY</div>
</section>

<section class="card card--back" aria-label="Card back">
  <div class="portrait" role="img" aria-label="Portrait photo of the agent in a dark suit"></div>
  <div class="info-panel"></div>
  <svg class="divider" viewBox="0 0 740 423" preserveAspectRatio="none" aria-hidden="true">
    <line x1="384.8" y1="0" x2="503.2" y2="423" stroke="var(--gold)" stroke-width="5"/>
  </svg>

  <div class="info">
    <div class="brand-name">EMBER REALTY</div>
    <h1 class="person__name">MARCUS HALE</h1>
    <p class="person__title">Managing Director</p>
    <ul class="contact">
      <li>
        <svg viewBox="0 0 24 24"><path d="M6.6 10.8a15.1 15.1 0 0 0 6.6 6.6l2.2-2.2a1 1 0 0 1 1-.25 11.4 11.4 0 0 0 3.6.57 1 1 0 0 1 1 1V20a1 1 0 0 1-1 1A17 17 0 0 1 3 4a1 1 0 0 1 1-1h3.5a1 1 0 0 1 1 1c0 1.25.2 2.45.57 3.57a1 1 0 0 1-.25 1z"/></svg>
        <span>044-987 654 321</span>
      </li>
      <li>
        <svg viewBox="0 0 24 24"><path d="M2 5h20v14H2z"/><path d="M2 6l10 7.5L22 6" fill="none" stroke="#fff" stroke-width="1.6"/></svg>
        <span>hello@emberrealty.com</span>
      </li>
      <li>
        <svg viewBox="0 0 24 24"><circle cx="12" cy="12" r="10"/><path d="M2 12h20M12 2c3 3 3 17 0 20M12 2c-3 3-3 17 0 20" fill="none" stroke="#fff" stroke-width="1.4"/></svg>
        <span>www.<span class="highlight">emberrealty</span>.com</span>
      </li>
    </ul>
    <p class="address">88 Harbor Lane, Suite 4<br>30118, Westland</p>
  </div>
</section>

</body>
</html>
```